New Company Business Card design

Looking for a corporate looking business card utilising my new logo design - the logo i would like embossed as one option and flat as another - simplistic but stylish - less is more - we are an import export business launching into the market - i would like a couple of options as main background - Grey or Black

```html
<!DOCTYPE html>
<html lang="en">
<head>
<meta charset="utf-8">
<title>Meridian Trade Partners – Business Card</title>
<link rel="stylesheet" href="https://fonts.googleapis.com/css2?family=Cinzel:wght@400;600&family=Arimo:wght@400&display=swap">
<style>
  :root {
    --page-bg: #e6e6e6;
    --card-grey: #6b6c70;
    --accent-blue: #1b75bc;
    --card-white: #f7f7f7;
    --text-light: #ffffff;
  }
  html, body {
    margin: 0;
    width: 1200px;
    height: 900px;
    overflow: hidden;
    background: var(--page-bg);
  }
  .card {
    position: absolute;
    left: 120px;
    top: 153px;
    width: 960px;
    height: 594px;
    overflow: hidden;
    box-shadow: 0 10px 30px rgba(0,0,0,0.18);
  }
  .card-shapes {
    position: absolute;
    inset: 0;
    width: 100%;
    height: 100%;
  }
  .holder {
    position: absolute;
    left: 59px;
    top: 68px;
    color: var(--text-light);
  }
  .holder-name {
    margin: 0;
    font-family: "Cinzel", serif;
    font-weight: 400;
    font-size: 32px;
    letter-spacing: 1px;
  }
  .holder-title {
    margin: 4px 0 0;
    font-family: "Arimo", sans-serif;
    font-size: 24px;
  }
  .contact-list {
    position: absolute;
    left: 59px;
    top: 382px;
    margin: 0;
    padding: 0;
    list-style: none;
    font-family: "Arimo", sans-serif;
    font-size: 24px;
    color: var(--text-light);
  }
  .contact-list li {
    display: flex;
    align-items: center;
    height: 34px;
    white-space: nowrap;
  }
  .contact-icon {
    width: 18px;
    height: 18px;
    margin-right: 12px;
    fill: var(--text-light);
  }
  .company-name {
    position: absolute;
    left: 480px;
    top: 262px;
    width: 420px;
    margin: 0;
    text-align: center;
    font-family: "Cinzel", serif;
    font-weight: 600;
    font-size: 32px;
    line-height: 1.15;
    letter-spacing: 1px;
    color: var(--accent-blue);
  }
  .company-mark {
    display: block;
    width: 70px;
    height: 70px;
    margin: 0 auto 16px;
    border-radius: 50%;
    background: var(--accent-blue);
  }
</style>
</head>
<body>
  <div class="card">
    <svg class="card-shapes" viewBox="0 0 652 403" preserveAspectRatio="none" aria-hidden="true">
      <rect width="652" height="403" fill="var(--card-white)"/>
      <circle cx="479" cy="228" r="236" fill="var(--accent-blue)"/>
      <circle cx="540" cy="262" r="261" fill="var(--card-white)"/>
      <path d="M0 0 H416 A236 236 0 0 0 321 403 H0 Z" fill="var(--card-grey)"/>
    </svg>

    <div class="holder">
      <h1 class="holder-name">DANIEL HART</h1>
      <p class="holder-title">Managing Director</p>
    </div>

    <ul class="contact-list">
      <li>
        <svg class="contact-icon" viewBox="0 0 18 18"><path d="M5 1h8a1 1 0 0 1 1 1v14a1 1 0 0 1-1 1H5a1 1 0 0 1-1-1V2a1 1 0 0 1 1-1zm1 2v10h6V3zm3 11a1 1 0 1 0 0 2 1 1 0 0 0 0-2z"/></svg>
        044-987 654 321
      </li>
      <li>
        <svg class="contact-icon" viewBox="0 0 18 18"><path d="M1 6c0-2 3-3 8-3s8 1 8 3v1.5h-4V6H5v1.5H1zM4 9l2-2h6l2 2v6H4zm5 1.5a2 2 0 1 0 0 4 2 2 0 0 0 0-4z"/></svg>
        044-987 654 321
      </li>
      <li>
        <svg class="contact-icon" viewBox="0 0 18 18"><path d="M1 4h16v10H1zm1.5 1.2L9 10l6.5-4.8V5h-13z"/></svg>
        info@meridiantp.com
      </li>
      <li>
        <svg class="contact-icon" viewBox="0 0 18 18"><circle cx="9" cy="9" r="8"/><path d="M5 5l3 1 1 3-2 1 1 4-3-2-1-4zM11 3l3 2-1 3-2-1z" fill="var(--card-grey)"/></svg>
        www.meridiantp.com
      </li>
    </ul>

    <p class="company-name">
      <span class="company-mark"></span>
      MERIDIAN TRADE<br>PARTNERS
    </p>
  </div>
</body>
</html>
```